Locksmith Business Cards

My father-in-law is in need of new business cards for his locksmith business and I need to impress him. Kindly help me out!

You can see the previous business card attached. It is a family run business in North Wales.

No individual names on the cards.

Key Things to Feature:
- The words "Prompt", "Local", "Reliable" (as you can see under the logo on the website)
- 24h Emergency Service
- Covering All of North Wales, the Wirral and Chester
- The color blue
- A key or a lock would be interesting (similar to the ones that come up when you google locksmith business card)

Optional (only if design includes bullet points, like the example below):
https://imgvaultcdn.net/samples/208314/55172/55172_3904821_208314_image.jpg
- Residential / Commercial / Automotive
- Alarms & Cameras
- Key Cutting & Safes

https://www.brynhafod-locksmiths.co.uk/

Industry/Entity Type

Locksmith

Contact Information for Business Card

01632 960 418
07700 900 362
brynhafodlocksmiths@mailvane.com
Brynhafod Locksmiths, The Willow Barn, 7 Tannery Rd., Llandudno LL99 4QX
www.brynhafod-locksmiths.co.uk

Requirements
Must have
• - The words "Prompt", "Local", "Reliable" (as you can see under the logo on the website)
• - 24h Emergency Service
• - Covering All of North Wales, the Wirral and Chester
Nice to have
• - A key or a lock would be interesting (similar to the ones that come up when you google locksmith business card)

```html
<!DOCTYPE html>
<html lang="en">
<head>
<meta charset="utf-8">
<title>Brynhafod Locksmiths – Business Cards</title>
<link rel="stylesheet" href="https://fonts.googleapis.com/css2?family=Open+Sans:wght@400;600;700;800&display=swap">
<style>
  :root{
    --navy:#252a6c;
    --navy-deep:#1c205a;
    --navy-soft:#33398a;
    --band:#4a5ca3;
    --accent:#5d6fbf;
    --paper:#ffffff;
    --backdrop:#2b2b2d;
  }
  *{box-sizing:border-box;margin:0;padding:0}
  html,body{width:1200px;height:1021px;overflow:hidden}
  body{background:var(--backdrop);font-family:"Open Sans",Arial,sans-serif;position:relative}

  .card{position:absolute;left:250px;width:700px;height:400px;overflow:hidden}

  /* Front */
  .card--front{top:60px;background:var(--navy);border-radius:90px 4px 4px 90px}
  .front__emblem{position:absolute;left:24px;top:24px;width:300px;height:352px;border-radius:70px;
    background:linear-gradient(160deg,#4a50a6 0%,var(--navy-soft) 35%,var(--navy-deep) 100%)}
  .front__info{position:absolute;left:340px;top:60px;width:340px;text-align:center;color:var(--paper)}
  .front__name{font-weight:800;font-size:38px;line-height:1.05;letter-spacing:1px;text-transform:uppercase}
  .front__est{display:flex;align-items:center;gap:12px;margin:16px 0 18px;color:var(--accent);font-size:18px}
  .front__est::before,.front__est::after{content:"";flex:1;height:2px;background:var(--accent)}
  .front__services{list-style:none;font-size:16.5px;line-height:1.45}
  .front__web{margin-top:22px;font-weight:700;font-size:17px}

  /* Back */
  .card--back{top:540px;background:var(--paper);border-radius:4px 110px 110px 4px}
  .back__brand{position:absolute;left:34px;top:34px;display:flex;align-items:center;gap:14px}
  .back__mark{width:52px;height:52px;background:var(--navy);border-radius:10px}
  .back__name{color:var(--navy);font-weight:800;font-size:25px;line-height:1.05;text-transform:uppercase;letter-spacing:.5px}
  .back__contact{position:absolute;left:34px;top:118px;list-style:none;color:var(--navy)}
  .back__contact li{display:flex;align-items:center;gap:10px}
  .back__contact svg{width:18px;height:18px;fill:var(--navy);flex:none}
  .back__phone{font-weight:800;font-size:24px;line-height:1.25}
  .back__email{font-size:16.5px;margin-top:4px}
  .back__address{position:absolute;left:34px;top:232px;color:var(--navy);font-size:16.5px;line-height:1.35}
  .back__coverage{position:absolute;left:0;top:290px;width:470px;height:64px;background:var(--band);
    color:var(--paper);font-size:17px;line-height:1.3;padding:8px 0 0 34px}
  .back__panel{position:absolute;left:430px;top:130px;width:250px;height:250px;background:var(--navy);
    border-radius:90px 30px 80px 30px}
  .back__tagline{position:absolute;left:36px;top:26px;width:178px;height:116px;background:var(--paper);
    border-radius:40px 40px 6px 6px;color:var(--navy);font-weight:800;font-size:22px;line-height:1.2;
    display:flex;flex-direction:column;justify-content:center;align-items:center}
  .back__hours{position:absolute;left:26px;top:170px;color:var(--paper);font-weight:800;font-size:40px}
  .back__emergency{position:absolute;left:128px;top:172px;color:var(--paper);font-weight:800;font-size:16px;line-height:1.15;text-align:center}
</style>
</head>
<body>

<section class="card card--front" aria-label="Front of card">
  <div class="front__emblem" role="img" aria-label="Large brand emblem area"></div>
  <div class="front__info">
    <h1 class="front__name">Brynhafod<br>Locksmiths</h1>
    <p class="front__est">Est Since 1989</p>
    <ul class="front__services">
      <li>Residential / Commercial / Automotive</li>
      <li>Alarms &amp; Cameras</li>
      <li>Key Cutting &amp; Safes</li>
    </ul>
    <p class="front__web">www.brynhafod-locksmiths.co.uk</p>
  </div>
</section>

<section class="card card--back" aria-label="Back of card">
  <div class="back__brand">
    <span class="back__mark"></span>
    <h2 class="back__name">Brynhafod<br>Locksmiths</h2>
  </div>
  <ul class="back__contact">
    <li class="back__phone">
      <svg viewBox="0 0 24 24" aria-hidden="true"><path d="M6.6 10.8a15.1 15.1 0 0 0 6.6 6.6l2.2-2.2a1 1 0 0 1 1-.25 11.4 11.4 0 0 0 3.6.57 1 1 0 0 1 1 1V20a1 1 0 0 1-1 1A17 17 0 0 1 3 4a1 1 0 0 1 1-1h3.5a1 1 0 0 1 1 1c0 1.25.2 2.45.57 3.57a1 1 0 0 1-.25 1z"/></svg>
      01632 960 418
    </li>
    <li class="back__phone">
      <svg viewBox="0 0 24 24" aria-hidden="true"><path d="M7 1h10a2 2 0 0 1 2 2v18a2 2 0 0 1-2 2H7a2 2 0 0 1-2-2V3a2 2 0 0 1 2-2zm0 3v14h10V4zm5 15.5a1 1 0 1 0 0 2 1 1 0 0 0 0-2z"/></svg>
      07700 900 362
    </li>
    <li class="back__email">
      <svg viewBox="0 0 24 24" aria-hidden="true"><path d="M2 5h20v14H2zm2 2v.4l8 5.2 8-5.2V7zm16 10V9.8l-8 5.2-8-5.2V17z"/></svg>
      brynhafodlocksmiths@mailvane.com
    </li>
  </ul>
  <p class="back__address">The Willow Barn, 7 Tannery Rd.<br>Llandudno LL99 4QX</p>
  <p class="back__coverage">Covering All of North Wales<br>the Wirral and Chester</p>
  <div class="back__panel">
    <p class="back__tagline"><span>Prompt.</span><span>Local.</span><span>Reliable</span></p>
    <p class="back__hours">24H</p>
    <p class="back__emergency">Emergency<br>Service</p>
  </div>
</section>

</body>
</html>
```